Velvet Ladle Wishes Website Design; Cupcake Business with a unique and bespoke design element

We need a website design for a new bespoke and unique business making gourmet cupcakes - but MOST IMPORTANTLY we design and handmake cupcake wrappers and toppers specifically for each client's event. We are based in Sydney, Australia. The final resulting website should be elegant yet whimsical reflecting the notion of dreams and very elegant events eg weddings and very special parties.

We want to eventually have about 5 pages, HOWEVER, this project is specifically for the first page (ie Home page) and one other only. The final required pages are: a HOME page; ABOUT US page; PHOTO GALLERY page; FLAVOUR MENU & OTHER PRODUCTS page; CONTACT & INTERNET ENQUIRY page.

We expect the HOME page to be quite elaborate, perhaps including some animation. We will be providing the text content for all the other pages, and basically they will have the same background as the home page. We are looking for a clean design that runs across each page thus giving the website a continuity that pulls it all together. We would like our logo to be included on each page.

PLEASE NOTE: We will want multiple pages worked on in the handover phase but initially we want a very concise, consistent template to limit the amount of work to prospective designers.

While we are primarily looking for the design phase to be covered by this project, we would certainly appreciate coding to be included and will take that into consideration when choosing a winner.
Updates

Hi Designers

We have added some more information to our brief - please review it.

Thanks and happy designing

Hi Designers

Please note that we have increased our Prize money to $750.00.  We hope this encourages you to participate.

Thanks and regards
Velvet Ladle Wishes

Hi Designers

We've just posted some photos to help give you an idea of what we do.  Please note our attention to detail and precision in our work.

Thanks
Velvet Ladle Wishes

Hi Designers

Please Note:  What makes us different  to any other cupcake business is that we design cupcake wrappers and toppers, unique to our client's event whether it be a wedding, a birthday party or product launch.  We consult with our client to understand themes, colours, styles etc.  We then have our designs printed, next they are cut by a specialised computerised cutting machine,  We assemble everything by hand, and usually embellish the wrapper and topper with pearls, crystals, feathers, lace, ribbons or whatever else is appropriate for the event.  All work is totally bespoke, unique and individual.  No other cupcake supplier that we know of goes to these lengths to satisfy their client's dreams.

THE WRAPPER AND TOPPER IS OUR PRIMARY SELLING POINT. 

PLEASE NOTE:- We have uploaded a new photograph which we want to be used as the main photograph on the landing page.

We have removed all previous photographs of cupcakes (except for one that we can't get rid of).

We don't want a picture of a cupcake on the landing page we want the image _D7C3239.jpg to be used for that purpose.

We have also uploaded our logo in a number of file formats as we have had requests from you for these.

Hi designers

we have a crazy busy weekend on and won't be able to make any decisions re our competition until Monday  -  sorry to keep you in suspense, just a couple more days please!

regards
Pam

Target Market(s)

Primarily women - brides, new mothers (Christenings), Event Planners, who place an emphasis on the beauty of a product rather than the cost

Industry/Entity Type

Events

Requirements
Must have
• It must have our Logo (see attached upload) on each page (our logo is a butterfly atop a cupcake resting on a spoon and our motto is "Creating Delicious Works of Art". The colours used are pale pink, blue and chocolate brown and we'd expect these colours to be repeated in the final website.
The website must have a photo gallery which we can access and add to/change as our business grows.
We need a contact page which has an "internet enquiry form".
There should be a "Menu" page describing our cupcake flavours.
The Home page must have a party/event feel to it - definitely making an enquirer want to enter further into the site.
Nice to have
• Our logo is attached below in the "uploads". One idea that we have had is to use the butterfly in the logo but start it as a caterpillar crawling on the screen; as it spins it's cocoon the words "Sweet Dreams Little Caterpillar" would appear on screen; this would incorporate the "Dreams" in our Business Name; then our logo butterfly would hatch. This encapsulates the idea of taking something plain (caterpillar/cupcake) and creating something beautiful (butterfly/OUR cupcake).
However, we are open to other design ideas.
The colours we would like to have are pale pink, blue and chocolate brown in the design.

Some websites we really admire are: www.mirabellhart.com www.ribbonglitterloaf.com.au and www.greetingsoriel.com.au
These websites have a lightness and sense of fantasy to them. They do not convey a corporate image at all, rather they make you want to be at the party.
Should not have
• No "Corporate" style.

Most Important: We already have a website which we are not happy with - that is why we are going through this exercise to replace it. That means we DO NOT want anything along the lines of our current website. We are expecting some fresh ideas for our prize money.

```html
<!DOCTYPE html>
<html lang="en">
<head>
<meta charset="utf-8">
<title>Velvet Ladle Wishes – About Us</title>
<link rel="stylesheet" href="https://fonts.googleapis.com/css2?family=Arimo:wght@400;700&family=Fondamento:ital@1&display=swap">
<style>
  :root {
    --blush: #fcdfe0;
    --blush-deep: #f6c9cf;
    --frosting: #f58fbd;
    --wrapper: #c9a79b;
    --plum: #73103a;
    --cocoa: #6b4b3e;
    --paper: #ffffff;
    --tile-light: #f4f2f2;
    --tile-dark: #d9d5d5;
    --photo-warm: #a39a8c;
    --photo-cool: #5d5a55;
  }
  * { box-sizing: border-box; margin: 0; padding: 0; }
  html, body { width: 1200px; height: 896px; overflow: hidden; }
  body { position: relative; font-family: "Arimo", Arial, sans-serif; background: var(--blush); }

  .backdrop {
    position: absolute; inset: 0 0 88px 0;
    background:
      radial-gradient(ellipse 170px 150px at 130px 80px, rgba(245,143,189,.75), rgba(201,167,155,.45) 60%, transparent 100%),
      radial-gradient(ellipse 150px 140px at 860px 60px, rgba(245,143,189,.7), rgba(201,167,155,.45) 60%, transparent 100%),
      radial-gradient(ellipse 140px 240px at 1150px 360px, rgba(245,143,189,.7), rgba(201,167,155,.4) 65%, transparent 100%),
      radial-gradient(ellipse 120px 220px at 60px 520px, rgba(245,143,189,.65), rgba(201,167,155,.4) 65%, transparent 100%),
      radial-gradient(ellipse 200px 110px at 1110px 760px, rgba(245,143,189,.7), transparent 100%),
      radial-gradient(ellipse 160px 90px at 360px 780px, rgba(245,143,189,.6), transparent 100%),
      linear-gradient(160deg, var(--blush) 0%, #fbd8da 60%, var(--blush-deep) 100%);
  }

  .brand {
    position: absolute; left: 440px; top: 14px; width: 350px; text-align: center;
  }
  .brand-dot {
    display: block; width: 100px; height: 100px; margin: 0 auto 18px;
    border-radius: 50%; background: #fbeef0;
  }
  .brand-name {
    font-family: "Arimo", Arial, sans-serif; font-size: 26px; line-height: 30px; font-weight: 400; color: var(--cocoa);
  }

  .social { position: absolute; top: 134px; left: 920px; display: flex; gap: 12px; list-style: none; }
  .social-tile {
    width: 45px; height: 45px; border-radius: 7px;
    background: linear-gradient(var(--tile-light), var(--tile-dark));
    box-shadow: 0 1px 3px rgba(0,0,0,.2);
  }

  .content-panel {
    position: absolute; left: 106px; top: 197px; width: 990px; height: 515px;
    background: var(--paper); box-shadow: 0 4px 14px rgba(0,0,0,.18);
  }
  .feature-photo {
    position: absolute; left: 37px; top: 28px; width: 354px; height: 460px;
    background: linear-gradient(180deg, var(--photo-warm) 0%, #8f877b 55%, var(--photo-cool) 100%);
  }
  .about {
    position: absolute; left: 435px; top: 52px; width: 505px; color: var(--cocoa);
  }
  .about-title {
    font-family: "Fondamento", cursive; font-style: italic; font-weight: 400; font-size: 40px; line-height: 48px;
    color: var(--plum); margin-bottom: 10px;
  }
  .about p {
    font-size: 14.6px; line-height: 20px; letter-spacing: 1.1px; margin-bottom: 19px; padding-left: 5px;
  }
  .page-links {
    position: absolute; left: 440px; top: 452px; font-size: 15px; letter-spacing: .9px; color: var(--plum);
  }
  .page-links a { color: var(--plum); text-decoration: none; }
  .page-links .sep { margin: 0 10px 0 6px; }

  .main-nav { position: absolute; left: 0; top: 738px; height: 70px; width: 900px; }
  .main-nav a {
    position: absolute; top: 0; height: 70px; line-height: 58px;
    font-family: "Fondamento", cursive; font-style: italic; font-size: 24px; color: var(--plum); text-decoration: none;
  }
  .main-nav a.is-active { background: var(--plum); color: var(--paper); width: 136px; text-align: center; }

  .sound-toggle { position: absolute; left: 930px; top: 735px; display: flex; align-items: flex-end; gap: 14px; }
  .sound-label { font-size: 13px; font-weight: 700; color: var(--plum); margin-bottom: 2px; letter-spacing: .5px; }

  .site-footer {
    position: absolute; left: 0; bottom: 0; width: 1200px; height: 88px; background: var(--plum);
    color: var(--paper); font-size: 11px; font-weight: 700; text-align: center; line-height: 96px;
  }
</style>
</head>
<body>
  <div class="backdrop" role="img" aria-label="Pale pink background scattered with large hand-drawn cupcakes and small hearts"></div>

  <header class="brand">
    <span class="brand-dot"></span>
    <div class="brand-name">Velvet Ladle Wishes</div>
  </header>

  <ul class="social" aria-label="Social links">
    <li class="social-tile" aria-label="Social profile one"></li>
    <li class="social-tile" aria-label="Social profile two"></li>
    <li class="social-tile" aria-label="Social profile three"></li>
  </ul>

  <main class="content-panel">
    <div class="feature-photo" role="img" aria-label="Photo of a birthday cupcake with a custom wrapper and topper beside a vintage camera and a jar of sweets"></div>
    <section class="about">
      <h1 class="about-title">About Us</h1>
      <p>Aliquam congue fermentum nisl. Mauris accumsan nulla vel diam. Sed in lacus ut enim adipiscing aliquet.</p>
      <p>Nulla venenatis. In pede mi, aliquet sit amet, euismod in, auctor ut, ligula. Aliquam dapibus tincidunt metus. Praesent justo dolor, lobortis quis, lobortis dignissim, pulvinar ac, lorem. Vestibulum sed ante. Donec sagittis euismod purus.</p>
      <p>Aliquam congue fermentum nisl. Mauris accumsan nulla vel diam. Sed in lacus ut enim adipiscing aliquet.</p>
      <p>Nulla venenatis. In pede mi, aliquet sit amet, euismod in, auctor ut, ligula. Aliquam dapibus tincidunt metus. Praesent justo dolor, lobortis quis, lobortis dignissim, pulvinar ac, lorem. Vestibulum sed ante. Donec sagittis euismod purus.</p>
    </section>
    <nav class="page-links"><a href="#">Home</a><span class="sep">|</span> <a href="#">Gallery</a></nav>
  </main>

  <nav class="main-nav">
    <a href="#" style="left:164px">Home</a>
    <a href="#" class="is-active" style="left:254px">About Us</a>
    <a href="#" style="left:417px">Gallery</a>
    <a href="#" style="left:534px">Flavour Menu</a>
    <a href="#" style="left:708px">Contact Us</a>
  </nav>

  <div class="sound-toggle">
    <svg width="48" height="40" viewBox="0 0 48 40" aria-hidden="true">
      <g fill="#73103a">
        <rect x="0" y="22" width="7" height="18"/>
        <rect x="10" y="14" width="7" height="26"/>
        <rect x="20" y="6" width="7" height="34"/>
        <rect x="30" y="0" width="7" height="40"/>
        <rect x="40" y="10" width="7" height="30"/>
      </g>
    </svg>
    <span class="sound-label">OFF &nbsp;|&nbsp; ON</span>
  </div>

  <footer class="site-footer">© Copyright 2012 &nbsp;|&nbsp; Velvet Ladle Wishes &nbsp;|&nbsp; All Rights Reserved</footer>
</body>
</html>
```